Realty Group Needs Classy, Contemporary Letterhead Design

We need a letterhead design for a new realty company located in NY, USA. We buy investment properties to rehabilitate and or keep in our rental portfolio.

```html
<!DOCTYPE html>
<html lang="en">
<head>
<meta charset="utf-8">
<title>Alderpoint Realty Group – Letterhead</title>
<link rel="stylesheet" href="https://fonts.googleapis.com/css2?family=Open+Sans:wght@400&family=Poppins:wght@400;500;700&display=swap">
<style>
  :root {
    --backdrop: #dedede;
    --paper: #f8f8f8;
    --brand: #4a2a86;
    --ink: #4a4a4a;
    --ink-soft: #5a5a5a;
    --signature-tone: #e6e4ea;
  }
  * { margin: 0; padding: 0; box-sizing: border-box; }
  html, body {
    width: 1153px; height: 1200px; overflow: hidden;
    background: var(--backdrop);
  }
  .letterhead {
    position: absolute; left: 167px; top: 30px;
    width: 818px; height: 1140px;
    background: var(--paper);
    box-shadow: 0 6px 24px rgba(0,0,0,0.12);
  }
  .brand {
    position: absolute; left: 73px; top: 70px; width: 240px;
    color: var(--brand);
    font-family: "Poppins", sans-serif; font-weight: 700;
    text-align: center; line-height: 1;
  }
  .brand-name { font-size: 31px; letter-spacing: -0.5px; display: block; }
  .brand-sub { font-size: 12px; letter-spacing: 1px; display: block; margin-top: 6px; }
  .contact {
    position: absolute; left: 517px; top: 76px;
    list-style: none;
    font-family: "Poppins", sans-serif; font-size: 15px;
    color: var(--ink); line-height: 19.5px;
  }
  .contact li { display: flex; align-items: center; gap: 5px; }
  .contact svg { width: 13px; height: 13px; fill: var(--brand); flex: none; }
  .letter-body {
    position: absolute; left: 73px; top: 270px; width: 670px;
    font-family: "Open Sans", sans-serif; font-size: 14.6px;
    line-height: 22px; color: var(--ink);
  }
  .letter-body p { margin-bottom: 22px; text-align: justify; }
  .letter-body .salutation, .letter-body .closing { text-align: left; }
  .signature-area {
    position: absolute; left: 73px; top: 850px; width: 100px; height: 90px;
    background: var(--signature-tone); border-radius: 4px;
  }
  .footer {
    position: absolute; left: 0; right: 0; top: 1060px;
    text-align: center; font-family: "Poppins", sans-serif;
    font-size: 15px; line-height: 20px; color: var(--ink-soft);
  }
  .footer-company { color: var(--brand); font-weight: 500; }
</style>
</head>
<body>
  <main class="letterhead">
    <div class="brand">
      <span class="brand-name">ALDERPOINT</span>
      <span class="brand-sub">Realty Group, LLC</span>
    </div>

    <ul class="contact">
      <li><svg viewBox="0 0 16 16" aria-hidden="true"><path d="M3 2h3l1.5 3.5-2 1.3a9 9 0 0 0 3.7 3.7l1.3-2L14 10v3a1.5 1.5 0 0 1-1.5 1.5C7 14.5 1.5 9 1.5 3.5A1.5 1.5 0 0 1 3 2z"/></svg>555.210.4870</li>
      <li><svg viewBox="0 0 16 16" aria-hidden="true"><path d="M1 3h14v10H1z M2 4l6 5 6-5" fill="var(--brand)"/><path d="M2 4.5l6 4.5 6-4.5" fill="none" stroke="#fff" stroke-width="1.2"/></svg>info@alderpointrealty.com</li>
      <li><svg viewBox="0 0 16 16" aria-hidden="true"><circle cx="8" cy="8" r="7"/><path d="M1 8h14M8 1c-3 3-3 11 0 14M8 1c3 3 3 11 0 14" fill="none" stroke="#fff" stroke-width="1"/></svg>www.alderpointrealty.com</li>
    </ul>

    <section class="letter-body">
      <p class="salutation">Dear customer,</p>
      <p>Lorem ipsum dolor sit amet, consectetur adipisicing elit, sed do eiusmod tempor incididunt ut labore et dolore magna aliqua. Ut enim ad minim veniam, quis nostrud exercitation ullamco laboris nisi ut aliquip ex ea commodo consequat. Duis aute irure dolor in reprehenderit in voluptate velit esse cillum dolore eu fugiat nulla pariatur. Excepteur sint occaecat cupidatat non proident, sunt in culpa qui officia deserunt mollit anim id est laborum.</p>
      <p>Lorem ipsum dolor sit amet, consectetur adipisicing elit, sed do eiusmod tempor incididunt ut labore et dolore magna aliqua. Ut enim ad minim veniam, quis nostrud exercitation ullamco laboris nisi ut aliquip ex ea commodo consequat. Duis aute irure dolor in reprehenderit in voluptate velit esse cillum dolore eu fugiat nulla pariatur. Excepteur sint occaecat cupidatat non proident, sunt in culpa qui officia deserunt mollit anim id est laborum.</p>
      <p>Lorem ipsum dolor sit amet, consectetur adipisicing elit, sed do eiusmod tempor incididunt ut labore et dolore magna aliqua. Ut enim ad minim veniam, quis nostrud exercitation ullamco laboris nisi ut aliquip ex ea commodo consequat. Duis aute irure dolor in reprehenderit in voluptate velit esse cillum dolore eu fugiat nulla pariatur. Excepteur sint occaecat cupidatat non proident, sunt in culpa qui officia deserunt mollit anim id est laborum.</p>
      <p>Lorem ipsum dolor sit amet, consectetur adipisicing elit, sed do eiusmod tempor incididunt ut labore et dolore magna aliqua. Ut enim ad minim veniam, quis nostrud exercitation ullamco laboris nisi ut aliquip ex ea commodo consequat. Duis aute irure dolor in reprehenderit.</p>
      <p class="closing">Yours Sincerely,</p>
    </section>

    <div class="signature-area" role="img" aria-label="Handwritten signature"></div>

    <footer class="footer">
      <div class="footer-company">Alderpoint Realty Group, LLC</div>
      <div>48 Harbor View Lane, Beacon, NY 12508</div>
    </footer>
  </main>
</body>
</html>
```